Kelvaro.ch is looking for business card letterhead and envelope C5 with WOW effect

We need a strong business card for our company Kelvaro.ch, logo is available. You want a black or dark background on which the logo Stark r% 26 # 252; appears. Letterhead and envelope in C5 format should be in a similar design, but does not have to be We need a strong business card for our company Kelvaro.ch, logo is available. A black or dark background is desired, on which the logo Stark comes across. The letterhead and the envelope in C5 format should have a similar design.

Target Market(s)

Private customers as well as entrepreneurs

Contact Information for Business Card

E-mail: info@kelvaro-example.ch
Web.www.Kelvaro-example.ch
Tel: +41 ( 0 ) 79 482 6037
Adresse:
Lindenweg 14
9406 Tarnbach

Hier kann man Icons verwenden für Email,Tel und Adressse

Font styles to use
Other font styles liked:
• Dubai,bold

Colors

Designer to choose colors to be used in the design.

Requirements
Must have
• WOW effect
Nice to have
• R% 26 # 252; back business card with our service listings. - VEHICLE LABELING - SHOP WINDOW LABELING - STICKERS AND MUCH MORE ... in red color

```html
<!DOCTYPE html>
<html lang="en">
<head>
<meta charset="utf-8">
<title>Kelvaro.ch — Stationery</title>
<link rel="stylesheet" href="https://fonts.googleapis.com/css2?family=Lato:wght@400;700;900&family=Open+Sans:wght@400;600&display=swap">
<style>
  :root {
    --ink: #0c0c0c;
    --yellow: #ffc81e;
    --paper: #ffffff;
    --stage: #e6e6e6;
    --text: #3a3a3a;
    --muted: #555555;
  }
  * { box-sizing: border-box; margin: 0; padding: 0; }
  html, body { width: 1200px; height: 1200px; overflow: hidden; }
  body { background: var(--stage); position: relative; font-family: "Open Sans", sans-serif; color: var(--text); }

  .sheet { position: absolute; background: var(--paper); box-shadow: 0 2px 10px rgba(0,0,0,.18); overflow: hidden; }

  .brand { display: flex; align-items: center; gap: 8px; position: absolute; }
  .brand-dot { width: 14px; height: 14px; border-radius: 50%; background: var(--yellow); }
  .brand-name { font-family: "Lato", sans-serif; font-weight: 900; color: var(--ink); letter-spacing: .5px; text-transform: uppercase; }

  /* Letterhead */
  .letterhead { left: 119px; top: 278px; width: 556px; height: 716px; }
  .letterhead .brand { left: 60px; top: 28px; }
  .letterhead .brand-name { font-size: 15px; }
  .letterhead .brand-dot { width: 28px; height: 28px; }

  .contact { position: absolute; top: 22px; font-family: "Lato", sans-serif; font-size: 10.5px; line-height: 12px; color: var(--ink); }
  .contact-address { left: 265px; top: 24px; border-left: 1px solid #777; padding-left: 8px; height: 34px; display: flex; gap: 4px; }
  .contact-lines { left: 373px; border-left: 1px solid #777; padding-left: 14px; height: 36px; }
  .contact-line { display: flex; align-items: center; gap: 4px; }
  .contact svg { width: 8px; height: 8px; flex: none; }

  .letter-body { position: absolute; left: 52px; top: 130px; width: 450px; font-size: 8.6px; line-height: 16px; color: var(--muted); }
  .letter-body p { margin-bottom: 16px; text-align: justify; }
  .letter-body .meta { line-height: 11px; margin-bottom: 10px; text-align: left; }
  .letter-body .recipient { margin-bottom: 28px; }
  .signature-mark { width: 128px; height: 18px; margin: -6px 0 6px; background: linear-gradient(90deg, #cfcfcf, #e8e8e8); border-radius: 2px; }
  .signer-name { font-size: 11px; color: var(--ink); line-height: 14px; }
  .signer-role { font-size: 8.6px; line-height: 18px; }

  .footer-band { position: absolute; left: 0; bottom: 0; width: 556px; height: 100px; display: block; }
  .services { position: absolute; right: 58px; bottom: 23px; text-align: right; font-family: "Lato", sans-serif; font-size: 11px; line-height: 13.5px; color: #fff; text-transform: uppercase; }
  .services li { list-style: none; display: flex; justify-content: flex-end; align-items: center; gap: 4px; }
  .services li::after { content: ""; width: 9px; height: 9px; border-radius: 50%; background: var(--yellow); }

  /* Envelope back */
  .envelope-back { left: 715px; top: 492px; width: 432px; height: 216px; }
  .envelope-back .brand { left: 28px; top: 22px; }
  .envelope-back .brand-dot { width: 20px; height: 20px; }
  .envelope-back .brand-name { font-size: 11.5px; }
  .envelope-band { position: absolute; left: 0; bottom: 0; width: 432px; height: 66px; display: block; }
  .envelope-address { position: absolute; left: 33px; bottom: 20px; font-family: "Lato", sans-serif; font-size: 8px; color: #fff; }

  /* Envelope front */
  .envelope-front { left: 717px; top: 742px; width: 429px; height: 214px; }
  .flap { position: absolute; left: 0; top: 0; width: 429px; height: 51px; display: block; }
  .flap-name { position: absolute; left: 0; right: 0; top: 12px; text-align: center; font-family: "Lato", sans-serif; font-weight: 900; font-size: 20px; color: var(--ink); letter-spacing: .5px; text-transform: uppercase; }
</style>
</head>
<body>

<section class="sheet letterhead">
  <div class="brand">
    <span class="brand-dot"></span>
    <span class="brand-name">Kelvaro.ch</span>
  </div>

  <div class="contact contact-address">
    <svg viewBox="0 0 10 14"><path d="M5 0a5 5 0 0 0-5 5c0 4 5 9 5 9s5-5 5-9a5 5 0 0 0-5-5zm0 7a2 2 0 1 1 0-4 2 2 0 0 1 0 4z" fill="#ffc81e"/></svg>
    <div>Lindenweg 14<br>9406 Tarnbach</div>
  </div>

  <div class="contact contact-lines">
    <div class="contact-line"><svg viewBox="0 0 10 10"><path d="M2 1l2 2-1 1.5c.6 1.2 1.3 1.9 2.5 2.5L7 6l2 2-1.5 1.5C4 9 1 6 .5 2.5z" fill="#ffc81e"/></svg>+41 ( 0 ) 79 482 6037</div>
    <div class="contact-line"><svg viewBox="0 0 10 8"><rect x="0" y="0" width="10" height="8" fill="#ffc81e"/><path d="M0 0l5 4 5-4" stroke="#fff" fill="none"/></svg>info@kelvaro-example.ch</div>
    <div class="contact-line"><svg viewBox="0 0 10 10"><circle cx="5" cy="5" r="5" fill="#ffc81e"/></svg>www.Kelvaro-example.ch</div>
  </div>

  <div class="letter-body">
    <p class="meta">Issuing Date: May 5, 2018</p>
    <p class="meta recipient">Name Of Employee Mr. XYZABC<br>Address of Employee<br>Address Line 2 etc..</p>
    <p class="meta" style="margin-bottom:16px">Dear Mr.XYZABC</p>
    <p>Lorem Ipsum has been the industry's standard dummy text ever since the 1500s, when an unknown printer took a galley of type and scrambled it to make a type specimen book. It has survived not only five centuries, but also the leap into electronic typesetting, remaining essentially unchanged. It was popularised in the 1960s with the release of Brevin sheets containing Lorem Ipsum passages, and more recently with desktop publishing software like Setwell Layout including versions of Lorem Ipsum.</p>
    <p>Lorem Ipsum is simply dummy text of the printing and typesetting industry. Lorem Ipsum has been the industry's standard dummy text ever since the 1500s, when an unknown printer took a galley of type and scrambled it to make a type specimen book.</p>
    <p>It has survived not only five centuries, but also the leap into electronic typesetting, remaining essentially unchanged. It was popularised in the 1960s with the release of Brevin sheets containing Lorem Ipsum passages.</p>
    <p class="meta" style="margin-top:26px">Yours Sincerely</p>
    <div class="signature-mark" role="img" aria-label="Handwritten signature"></div>
    <div class="signer-name">Marten Keller</div>
    <div class="signer-role">Managing Director</div>
  </div>

  <svg class="footer-band" viewBox="0 0 556 100" preserveAspectRatio="none" aria-hidden="true">
    <polygon points="0,22 556,4 556,10 0,28" fill="var(--yellow)"/>
    <polygon points="0,34 556,16 556,100 0,100" fill="var(--ink)"/>
  </svg>
  <ul class="services">
    <li>Vehicle Labeling</li>
    <li>Shop Window Labeling</li>
    <li>Stickers and much more</li>
  </ul>
</section>

<section class="sheet envelope-back">
  <div class="brand">
    <span class="brand-dot"></span>
    <span class="brand-name">Kelvaro.ch</span>
  </div>
  <svg class="envelope-band" viewBox="0 0 432 66" preserveAspectRatio="none" aria-hidden="true">
    <polygon points="0,4 432,4 432,8 0,8" fill="var(--yellow)"/>
    <rect x="0" y="12" width="432" height="54" fill="var(--ink)"/>
  </svg>
  <div class="envelope-address">Lindenweg 14,9406 Tarnbach</div>
</section>

<section class="sheet envelope-front">
  <svg class="flap" viewBox="0 0 429 51" preserveAspectRatio="none" aria-hidden="true">
    <path d="M0 0 L429 0 L412 51 L17 51 Z" fill="var(--yellow)"/>
  </svg>
  <div class="flap-name">Kelvaro.ch</div>
</section>

</body>
</html>
```